Change English consent to translated Arabic and Persian on adobe indesign.

I need two consent forms done.
First one needs English replaced wiht arabic
Second one needs English replaced with persian

I will send the indesign once you accept the project as the file is large.
I have attached the translation.
No real graphics need to be done.

Please get Adobe Indesign file from this link
https://sendvault.net/470291638

The translations are attached to this project.

```html
<!DOCTYPE html>
<html lang="ar" dir="rtl">
<head>
<meta charset="utf-8">
<title>نموذج استمارة الموافقة</title>
<link href="https://fonts.googleapis.com/css2?family=Tajawal:wght@400;500;700;800&display=swap" rel="stylesheet">
<style>
  :root{
    --blue:#1b9ad6;
    --ink:#2b2b2b;
    --muted:#6d6d6d;
    --line:#9a9a9a;
    --paper:#ffffff;
  }
  *{box-sizing:border-box;margin:0;padding:0}
  html,body{width:849px;height:1200px;overflow:hidden;background:var(--paper)}
  body{font-family:"Tajawal",sans-serif;color:var(--ink);font-size:12px;line-height:1.45;position:relative}
  .page{position:absolute;inset:0;padding:30px 40px 0 40px}

  .masthead{display:flex;justify-content:flex-start;direction:ltr;height:96px;align-items:center}
  .brand{display:flex;align-items:center;gap:10px;font-weight:700;font-size:30px;color:var(--blue)}
  .brand .dot{width:16px;height:16px;border-radius:50%;background:var(--blue)}

  .form-title{font-weight:700;font-size:13px;margin-top:6px}
  .privacy-bar{background:var(--blue);color:#fff;font-weight:700;font-size:16px;padding:6px 12px;margin-top:5px}

  .details{display:grid;grid-template-columns:1fr 1fr;gap:34px;margin-top:14px}
  .section-label{font-weight:800;font-size:13px;border-bottom:2px solid var(--blue);padding-bottom:2px;margin-bottom:4px}
  .field{display:flex;gap:6px;align-items:flex-end;height:22px;font-size:11.5px}
  .field span{white-space:nowrap}
  .field i{flex:1;border-bottom:1px dotted var(--line);height:14px}
  .note{font-size:10.5px;color:var(--muted);margin-top:8px;display:flex;justify-content:space-between}

  .consent{margin-top:22px}
  .consent h2,.questions h2{font-size:14px;font-weight:800;border-bottom:2px solid var(--blue);padding-bottom:3px;margin-bottom:10px}
  .tick-row{display:flex;gap:8px;align-items:flex-start;font-size:11.5px;margin-bottom:8px}
  .box{width:13px;height:13px;border:1.3px solid var(--ink);flex:none;margin-top:2px;background:#fff}

  .questions{margin-top:22px}
  .q{font-size:11.5px;margin-bottom:5px}
  .answer{display:flex;align-items:center;gap:22px;font-size:11px;margin:5px 0 14px}
  .answer .opt{display:flex;gap:6px;align-items:center}
  .answer .detail{flex:1;display:flex;gap:6px;align-items:flex-end}
  .answer .detail i{flex:1;border-bottom:1px dotted var(--line);height:12px}

  .declaration{margin-top:14px;border-top:2px solid var(--blue);padding-top:10px;font-size:11px}
  .declaration li{margin-right:14px;margin-bottom:6px}
  .signatures{display:grid;grid-template-columns:1fr 1fr;gap:34px;row-gap:22px;margin-top:16px}
  .signatures .field{height:26px}

  .footer{position:absolute;bottom:18px;left:40px;right:40px;border-top:1px solid var(--line);padding-top:4px;font-size:9px;color:var(--muted);display:flex;justify-content:space-between}
</style>
</head>
<body>
<main class="page">
  <header class="masthead">
    <div class="brand"><span class="dot"></span>Nuvaro Clinics</div>
  </header>

  <h1 class="form-title">نموذج استمارة الموافقة على الفوائد المجمعة لخدمات برنامج العناية بأسنان الأطفال</h1>
  <div class="privacy-bar">سوف يتم الاحتفاظ بسرية وخصوصية كافة المعلومات والبيانات</div>

  <section class="details">
    <div class="patient">
      <div class="section-label">بيانات المريض</div>
      <div class="field"><span>اللقب:</span><i></i></div>
      <div class="field"><span>الاسم الأول:</span><i></i></div>
      <div class="field"><span>تاريخ الميلاد:</span><i></i></div>
      <div class="field"><span>اسم الأم / الأب / ولي الأمر:</span><i></i></div>
      <div class="field"><span>العنوان:</span><i></i></div>
      <div class="field"><span>الضاحية:</span><i></i></div>
      <div class="field"><span>الرمز البريدي:</span><i></i></div>
      <div class="field"><span>البريد الإلكتروني:</span><i></i></div>
      <div class="field"><span>رقم البطاقة الصحية:</span><i></i></div>
    </div>
    <div class="unit">
      <div class="section-label">رقم الوحدة</div>
      <div class="field"><span>الصف:</span><i></i></div>
      <div class="field"><span>الجنس:</span><i></i></div>
      <div class="field"><span>اسم مدرسة الطفل:</span><i></i></div>
      <div class="field"><span>هاتف المنزل:</span><i></i></div>
      <div class="field"><span>الهاتف الجوال:</span><i></i></div>
      <div class="field"><span>اسم الطبيب العام:</span><i></i></div>
      <div class="field"><span>رقم البطاقة الطبية:</span><i></i></div>
      <div class="field"><span>الرقم المرجعي:</span><i></i></div>
      <div class="field"><span>تاريخ الانتهاء:</span><i></i></div>
    </div>
  </section>
  <div class="note"><span>هل لدى الطفل بطاقة رعاية صحية سارية المفعول؟ نعم ☐ لا ☐</span><span>هل يعتبر الطفل من سكان السكان الأصليين؟ نعم ☐ لا ☐</span></div>

  <section class="consent">
    <h2>يرجى وضع علامة (✓) في خانة الموافقة على ما يلي</h2>
    <div class="tick-row"><span class="box"></span><span>أوافق على قيام فريق العيادة المتنقلة بتقديم خدمات فحص الأسنان للطفل المذكور أعلاه وفقاً لبرنامج الرعاية المعتمد عند الحاجة.</span></div>
    <div class="tick-row"><span class="box"></span><span>أوافق على قيام الفريق بإجراء تقييم لحالة الأسنان، بما في ذلك التصوير وتنظيف الأسنان ووضع الفلورايد.</span></div>
    <div class="tick-row"><span class="box"></span><span>لا أرغب في مشاركة طفلي في برنامج العناية بالأسنان.</span></div>
  </section>

  <section class="consent">
    <h2>يرجى وضع علامة (✓) في خانة الموافقة على ما يلي</h2>
    <div class="tick-row"><span class="box"></span><span>أوافق على استخدام الفوائد الخاصة بطفلي من خلال برنامج KDSP لتغطية تكاليف العلاج.</span></div>
    <div class="tick-row"><span class="box"></span><span>أؤكد أن طفلي مؤهل للحصول على خدمات برنامج KDSP وأن المعلومات المقدمة صحيحة.</span></div>
    <div class="tick-row"><span class="box"></span><span>أوافق على التواصل معي عبر الهاتف عند الحاجة إلى علاج إضافي لطفلي.</span></div>
  </section>

  <section class="questions">
    <h2>يرجى إكمال ما يلي</h2>
    <p class="q">هل تلقى الطفل أي علاج للأسنان خلال السنة الماضية؟</p>
    <div class="answer"><span class="opt"><span class="box"></span>نعم</span><span class="opt"><span class="box"></span>لا</span><span class="detail"><span>يرجى ذكر التفاصيل:</span><i></i></span></div>
    <p class="q">هل يعاني الطفل من أي أمراض أو حساسية؟</p>
    <div class="answer"><span class="opt"><span class="box"></span>نعم</span><span class="opt"><span class="box"></span>لا</span><span class="detail"><span>يرجى ذكر التفاصيل:</span><i></i></span></div>
    <p class="q">هل يتناول الطفل أي أدوية حالياً؟</p>
    <div class="answer"><span class="opt"><span class="box"></span>نعم</span><span class="opt"><span class="box"></span>لا</span><span class="detail"><span>يرجى ذكر التفاصيل:</span><i></i></span></div>
  </section>

  <section class="declaration">
    <ul>
      <li>أقر بأنني قرأت وفهمت المعلومات الواردة في هذا النموذج وأن جميع البيانات المقدمة صحيحة وكاملة.</li>
      <li>أفهم أنه يمكنني سحب موافقتي في أي وقت عن طريق إبلاغ العيادة كتابياً.</li>
      <li>أوافق على أن يتم حفظ السجلات الطبية لطفلي بسرية تامة وفقاً لقوانين الخصوصية المعمول بها.</li>
    </ul>
    <div class="signatures">
      <div class="field"><span>توقيع الأب / الأم / ولي الأمر:</span><i></i></div>
      <div class="field"><span>التاريخ:</span><i></i></div>
      <div class="field"><span>اسم الشخص الذي قام بالتوقيع:</span><i></i></div>
      <div class="field"><span>صلة القرابة:</span><i></i></div>
    </div>
  </section>

  <footer class="footer">
    <span>شكراً لتعاونكم — يرجى إعادة النموذج إلى مدرسة الطفل</span>
    <span>نسخة ٢٠١٩</span>
  </footer>
</main>
</body>
</html>
```